New Corporate Email footer (business card design) for 40th Anniversary for Timber Traders

We are traders in sustainable timber worldwide, specialising in tropical hardwoods.
We need to keep our current company logo, but update our email footer with a business card like design which marks the company's 40th Anniversary. 1981-2021. We would need:
Company Logo, Name and Address, website
Sender's: Name, Tel no, fax no, email address
We would need this in a format which we could update ourselves re names/phone numbers if any change.

Target Market(s)

Customers, suppliers, service providers

Contact Information for Business Card

Mavis Thorne
Tel: +44 (0) 208 473 2586
Fax: +44 (0) 208 473 5820
Email: mavis@pwlwoods.co.uk
Web: www.pwlwoods.co.uk

PWL Woods Ltd. 7 Falcon Court, Birchmore Way, Oakwick, Surrey CR4 6TJ, UNITED KINGDOM

IMPORTANT NOTICE - This message contains confidential information for the intended addressee only. Any views expressed are those of the sender not PWL Woods Ltd unless otherwise stated. If you receive this message [and any attachment(s)] in error you must not store, copy, disclose or otherwise use any part of it and should advise the sender immediately on 020 8473 9152. Internet communications are not guaranteed secure or virus free. PWL reserves the right to monitor all e-mail communications and does not accept responsibility for any loss or damage resulting from access of this e-mail or any file(s) attached.

Font styles to use
Sans Serif
Other font styles liked:
• not actually sure

Requirements
Must have
• mention of company's 40th Anniversary 1981-2021, which is the whole point of the design
Nice to have
• Our company colour is British Racing Green, but any green theme may be good
Maybe a tree design but allowing the company logo to stand out.

```html
<!DOCTYPE html>
<html lang="en">
<head>
<meta charset="UTF-8">
<title>PWL Woods Ltd — 40th Anniversary Business Card</title>
<link rel="stylesheet" href="https://fonts.googleapis.com/css2?family=Arimo:wght@400;700&family=Montserrat:wght@600&display=swap">
<style>
  :root {
    --stage: #2b2b2b;
    --ink: #141414;
    --paper: #ffffff;
    --faint: #f1f1f1;
    --gold-light: #fbe89a;
    --gold-mid: #eab24c;
    --gold-deep: #c98a2a;
    --gold-dark: #a8701e;
    --seal-core: #231a0c;
    --rule: #1c1c1c;
  }
  * { margin: 0; padding: 0; box-sizing: border-box; }
  html, body { width: 1200px; height: 900px; overflow: hidden; }
  body {
    background: var(--stage);
    font-family: "Arimo", Arial, sans-serif;
    color: var(--ink);
    position: relative;
  }
  .card {
    position: absolute;
    width: 640px;
    height: 366px;
    border-radius: 24px;
    overflow: hidden;
  }
  /* Front */
  .card--front {
    left: 280px;
    top: 44px;
    background: linear-gradient(110deg, var(--gold-mid) 0%, var(--gold-light) 38%, var(--gold-mid) 62%, var(--gold-light) 85%, var(--gold-deep) 100%);
    display: flex;
    align-items: center;
    justify-content: center;
  }
  .brand {
    display: flex;
    align-items: center;
    gap: 14px;
  }
  .brand__dot {
    width: 64px;
    height: 64px;
    border-radius: 50%;
    background: var(--ink);
  }
  .brand__name {
    font-family: "Arimo", Arial, sans-serif;
    font-weight: 700;
    font-size: 58px;
    letter-spacing: 2px;
    color: var(--ink);
    line-height: 1;
  }
  /* Back */
  .card--back {
    left: 280px;
    top: 490px;
    background: var(--paper);
  }
  .card__edge {
    position: absolute;
    left: 0; right: 0; bottom: 0;
    height: 16px;
    background: linear-gradient(90deg, var(--gold-dark), var(--gold-light) 35%, var(--gold-deep) 70%, var(--gold-light));
  }
  .faint-name {
    position: absolute;
    right: 40px;
    top: 70px;
    font-family: "Arimo", Arial, sans-serif;
    font-weight: 700;
    font-size: 96px;
    line-height: 1;
    color: var(--faint);
    letter-spacing: 4px;
  }
  .holder-name {
    position: absolute;
    right: 44px;
    top: 36px;
    font-family: "Montserrat", Arial, sans-serif;
    font-weight: 600;
    font-size: 22px;
    letter-spacing: 1px;
    text-transform: uppercase;
  }
  .card--back .brand {
    position: absolute;
    left: 40px;
    top: 118px;
  }
  .card--back .brand__dot { width: 54px; height: 54px; }
  .card--back .brand__name { font-size: 48px; }
  .divider {
    position: absolute;
    left: 40px;
    right: 40px;
    top: 200px;
    height: 1px;
    background: var(--rule);
  }
  .contact {
    position: absolute;
    left: 40px;
    top: 214px;
    list-style: none;
    font-size: 17px;
    line-height: 28px;
  }
  .contact li { display: flex; align-items: center; gap: 10px; }
  .contact__icon {
    width: 18px;
    height: 18px;
    border-radius: 3px;
    background: linear-gradient(135deg, var(--gold-light), var(--gold-deep));
    display: flex;
    align-items: center;
    justify-content: center;
  }
  .contact__icon svg { width: 12px; height: 12px; }
  .anniversary-seal {
    position: absolute;
    right: 48px;
    top: 212px;
    width: 124px;
    height: 124px;
    border-radius: 50%;
    background: var(--seal-core);
    border: 4px solid var(--gold-mid);
    box-shadow: inset 0 0 0 3px var(--seal-core), inset 0 0 0 5px var(--gold-deep);
    display: flex;
    flex-direction: column;
    align-items: center;
    justify-content: center;
    color: var(--gold-light);
    text-align: center;
  }
  .seal__years {
    font-size: 11px;
    font-weight: 700;
    letter-spacing: 1px;
  }
  .seal__number {
    font-size: 44px;
    font-weight: 700;
    line-height: 1;
    color: var(--gold-mid);
  }
  .seal__number sup {
    font-size: 14px;
    vertical-align: top;
    position: relative;
    top: 4px;
  }
  .seal__label {
    font-size: 10px;
    font-weight: 700;
    letter-spacing: 1.5px;
    text-transform: uppercase;
  }
</style>
</head>
<body>
  <section class="card card--front" aria-label="Card front">
    <div class="brand">
      <span class="brand__dot"></span>
      <span class="brand__name">PWL</span>
    </div>
  </section>

  <section class="card card--back" aria-label="Card back">
    <span class="faint-name" aria-hidden="true">PWL</span>
    <h1 class="holder-name">Mavis Thorne</h1>
    <div class="brand">
      <span class="brand__dot"></span>
      <span class="brand__name">PWL</span>
    </div>
    <div class="divider"></div>
    <ul class="contact">
      <li><span class="contact__icon"><svg viewBox="0 0 12 12"><path d="M3 1l2 2-1 1.5c.8 1.6 1.9 2.7 3.5 3.5L9 7l2 2-1.5 2C5 10.5 1.5 7 1 2.5z" fill="#fff"/></svg></span>+44 (0) 208 473 2586</li>
      <li><span class="contact__icon"><svg viewBox="0 0 12 12"><rect x="2" y="4" width="8" height="6" rx="1" fill="#fff"/><rect x="3.5" y="1.5" width="5" height="3" fill="none" stroke="#fff"/></svg></span>+44 (0) 208 473 5820</li>
      <li><span class="contact__icon"><svg viewBox="0 0 12 12"><rect x="1" y="3" width="10" height="7" fill="#fff"/><path d="M1 3l5 4 5-4" fill="none" stroke="#c98a2a"/></svg></span>mavis@pwlwoods.co.uk</li>
      <li><span class="contact__icon"><svg viewBox="0 0 12 12"><circle cx="6" cy="6" r="4.5" fill="none" stroke="#fff" stroke-width="1.3"/><path d="M1.5 6h9M6 1.5c-2 3-2 6 0 9M6 1.5c2 3 2 6 0 9" fill="none" stroke="#fff"/></svg></span>www.pwlwoods.co.uk</li>
    </ul>
    <div class="anniversary-seal" aria-label="40th Anniversary, 1981–2021">
      <span class="seal__years">1981–2021</span>
      <span class="seal__number">40<sup>th</sup></span>
      <span class="seal__label">Anniversary</span>
    </div>
    <div class="card__edge"></div>
  </section>
</body>
</html>
```